Create Website for new company called "Verdale Lodge 37"

Verdale Lodge 37 is a new business situated in Southwestern Colorado. We are creating a business that will rent out spaces where clients can grow their own marijuana. Picture a large green house with partitioned spaces that are secured by a lock. Best way to envision this would be to think of a storage business that rents out storage rooms. The difference is that we will be having the units inside a green house ( for growing purposes) Picture a small area that is secured by locks, Picture an area that has the ability to provide state of the art security, cameras etc. We want to focus our efforts on professionals, blue collar workers and end users of marijuana. Our emphasis is in the area of assisting those whom wish to grow their own plants. We want to provide them a safe facility in which to do that. . Keep in mind that we also build custom grow rooms at clients homes and provide a grow pod (lease these) where a small grow unit will be delivered and picked up from our clients whom want to lease a unit for a short amount of time. We have a business card ( just designed) and will send that information to those whom express an interests in this project. We want to be able to sign people up for our services by entering an agreement and signing the agreement while on the internet. We want to provide our services to those whom consume recreational and medical marijuana. This site will need to gather information I.e email addresses so that we can followup with offers. This is a tremendous opportunity for the right designer. We will be creating many more websites as other states come on line and make marijuana legal to consume. Use the business card model for a point of reference of how we envision the concept. That is a business card we just recently printed. The hands and the plant is our logo so far. Open to suggestions. There will be three levels of service. Bronze, Silver, Gold or Platinum. We will also have a retail biz down the road but not at the present time.

Target Market(s)

Ages 21-60

Industry/Entity Type

Medical

Logo Text

Verdale Lodge 37.

Number of Pages Required

5+ page

Requirements
Must have
• Clean appearance not to busy , easily navigable from link to link, page to page. Must have ability down the road to enter into a contractual agreement via the website. Must use our provided logo and example of that is on our business card that will be uploaded here shortly. We would like to have the colors that are on the business card however if you have suggestions or color schemes that you want us to consider that is okay.
Nice to have
• Nice to have a animation of seed to weed and how clients can save a tremendous amount of money growing their own cannabis. Nice to have testimonial page or feedback page. Have a membership component to website,
Should not have
• No flashing lights, etc. Not to busy in terms of animations.

```html
<!DOCTYPE html>
<html lang="en">
<head>
<meta charset="utf-8">
<title>Verdale Lodge 37</title>
<link href="https://fonts.googleapis.com/css2?family=Oswald:wght@400;500&family=Roboto:ital,wght@0,300;0,400;1,300;1,400&display=swap" rel="stylesheet">
<style>
:root{
  --orange:#c0772a;
  --green:#2e7d3a;
  --ink:#3d3d3d;
  --body:#555;
  --beige:#f0d5b6;
  --dark:#2d2f2f;
  --line:#d7bfa3;
}
*{box-sizing:border-box;margin:0;padding:0}
html,body{width:891px;height:1200px;overflow:hidden;background:#fff}
body{position:relative;font-family:'Roboto',sans-serif;color:var(--body)}
.abs{position:absolute}
.h{font-family:'Oswald',sans-serif;font-weight:400;color:var(--ink);text-transform:uppercase;letter-spacing:-.2px;white-space:nowrap}
.h span{color:var(--green)}
.brand{left:55px;top:28px;font-family:'Oswald',sans-serif;font-weight:500;font-size:24px;color:#3a3a3a;letter-spacing:.3px;display:flex;align-items:center;gap:8px}
.brand i{display:block;width:16px;height:16px;border-radius:50%;background:var(--green)}
.login{right:56px;top:15px;font-size:8px;color:#666;letter-spacing:.3px}
.login:after{content:"";display:inline-block;margin-left:6px;border:3.5px solid transparent;border-top:4px solid #666;vertical-align:-2px}
.call{right:55px;top:40px;font-size:13px;color:var(--orange);display:flex;align-items:center;gap:6px}
.call b{font-weight:400;color:var(--green);font-size:15.5px}
.call svg{margin-right:2px}
.hero{left:0;top:98px;width:891px;height:313px;background:linear-gradient(180deg,#8f9a8c 0%,#b9c2b3 18%,#6f8e4a 40%,#4f7a2c 65%,#6b9a3d 100%)}
.nav{left:55px;top:81px;width:781px;height:34px;background:var(--orange);display:flex;z-index:2;box-shadow:0 2px 4px rgba(0,0,0,.25)}
.nav a{font-family:'Oswald',sans-serif;font-size:12.5px;color:#fff;text-decoration:none;text-transform:uppercase;line-height:34px;padding:0 15px;margin-right:16px;white-space:nowrap}
.nav a.on{background:#2e3030}
.nav a:last-child{margin-right:0}
.headline{left:0;top:212px;width:891px;text-align:center;font-family:'Oswald',sans-serif;font-weight:400;font-size:32px;line-height:38px;color:#fff;text-shadow:0 2px 4px rgba(0,0,0,.45)}
.dots{left:416px;top:385px;display:flex;gap:7px}
.dots i{width:10px;height:10px;border-radius:50%;background:#fff}
.dots i:first-child{background:var(--orange)}
p.txt{font-size:10px;line-height:15.8px;font-weight:300;color:#444}
.btn{display:block;background:var(--orange);color:#fff;font-family:'Oswald',sans-serif;font-size:11px;text-transform:uppercase;text-align:center;line-height:27px;width:88px;height:27px}
.photo{border:2px solid #d8c4ab;background:linear-gradient(135deg,#6f9a3e,#3e6a26 60%,#2c4a20)}
.welcome-photo{left:591px;top:443px;width:245px;height:150px;border-color:#ddd;background:linear-gradient(160deg,#a6a692 0%,#6f8c3a 35%,#3e6a24 100%)}
.band{left:0;top:613px;width:891px;height:349px;background:var(--beige)}
.arrows{display:flex;gap:13px}
.arrows svg{display:block}
.divider{left:322px;top:791px;width:514px;height:1px;background:var(--line)}
.date{font-size:9.5px;color:var(--green)}
.news p{font-size:9.6px;line-height:15.8px;font-weight:300;color:#444;margin-top:3px}
.more{font-size:8px;color:var(--orange);text-transform:uppercase;margin-top:7px;letter-spacing:.3px}
.thumb{width:73px;height:60px}
.quote{font-style:italic;font-size:9.6px;line-height:16px;color:#444;font-weight:300}
.rent{left:590px;top:986px;width:246px;height:111px;background:linear-gradient(135deg,#c9812f,#a8601c);border:1px solid #9b5a1c}
.rent h3{font-family:'Oswald',sans-serif;font-weight:400;color:#fff;font-size:18px;line-height:25px;text-transform:uppercase;position:absolute;left:17px;top:11px}
.rent .get{position:absolute;left:17px;top:69px;width:101px;height:26px;background:#f3ddc2;color:#5a3a1a;font-family:'Oswald',sans-serif;font-size:11px;line-height:26px;text-align:center;text-transform:uppercase}
.rent .mapart{position:absolute;left:152px;top:38px;width:80px;height:66px;border-radius:3px;background:linear-gradient(135deg,#9fd27a,#5aa3d6)}
.footer{left:0;top:1122px;width:891px;height:78px;background:var(--dark)}
.footer .fbrand{position:absolute;left:55px;top:15px;font-family:'Oswald',sans-serif;font-weight:500;font-size:15px;color:#ddd;display:flex;align-items:center;gap:6px}
.footer .fbrand i{display:block;width:10px;height:10px;border-radius:50%;background:var(--green)}
.footer small{position:absolute;left:55px;top:53px;font-size:7.5px;font-style:italic;color:#bbb}
.connect{position:absolute;left:682px;top:33px;font-size:10px;color:#ddd;letter-spacing:.4px;display:flex;align-items:center;gap:8px}
.connect i{display:block;width:24px;height:24px;border-radius:50%}
</style>
</head>
<body>

<header>
  <div class="abs brand"><i></i>Verdale Lodge 37</div>
  <div class="abs login">CLIENT LOG IN</div>
  <div class="abs call">
    <svg width="14" height="14" viewBox="0 0 14 14"><rect width="14" height="14" rx="2" fill="#cfcfcf"/><path d="M4 3c1 0 1.5 2 1 2.5l-.7.6c.6 1.3 1.4 2.1 2.6 2.7l.6-.7c.5-.5 2.5 0 2.5 1 0 1-1 1.9-2 1.9C5.2 11 3 8.8 3 5c0-1 .9-2 1-2z" fill="#fff"/></svg>
    Call Us: <b>555-014-2290</b>
  </div>
</header>

<div class="abs hero" role="img" aria-label="Photo of a greenhouse full of young cannabis plants under hanging lamps"></div>

<nav class="abs nav">
  <a class="on">Home</a><a>About Us</a><a>Services</a><a>Latest News</a><a>Gallery</a><a>Blog</a><a>Testimonials</a><a>Contact Us</a>
</nav>

<h1 class="abs headline">We are creating a business that will rent out spaces where<br>clients can grow their own marijuana</h1>
<div class="abs dots"><i></i><i></i><i></i><i></i></div>

<section>
  <h2 class="abs h" style="left:55px;top:436px;font-size:20px">Welcome to <span>Verdale Lodge</span></h2>
  <p class="abs txt" style="left:55px;top:471px;width:510px">Aliquam molestie, mi et imperdiet euismod, dui purus auctor tellus, et interdum lacus lectus et ante. Sed accumsan sollicitudin sapien, sit amet adipiscing turpis gravida ac. In congue, neque ac lobortis volutpat, libero mauris varius mi, vitae suscipit ipsum ligula vitae risus. Duis aliquam nibh a dui iaculis viverra id a velit. Vivamus egestas risus in magna varius commodo. Sed semper viverra egestas. Etiam pretium porttitor lectus, vel ornare neque porta volutpat.</p>
  <a class="abs btn" style="left:55px;top:566px">Read More</a>
  <div class="abs photo welcome-photo" role="img" aria-label="Photo of flowering cannabis plants in an indoor grow room"></div>
</section>

<div class="abs band"></div>

<section>
  <h2 class="abs h" style="left:55px;top:636px;font-size:20px">What <span>Verdale Lodge</span> do?</h2>
  <div class="abs photo" style="left:55px;top:673px;width:235px;height:117px" role="img" aria-label="Photo of a grower tending plants in a greenhouse"></div>
  <p class="abs txt" style="left:55px;top:802px;width:236px">Aliquam molestie, mi et imperdiet euismod, dui purus auctor tellus, et interdum lacus lectus et ante. Sed accumsan sollicitudin sapien, sit amet adipiscing turpis gravida ac. In congue, neque ac lobortis volutpat, libero mauris varius mi, vitae suscipit ipsum ligula itae risus.</p>
  <a class="abs btn" style="left:55px;top:912px">Read More</a>
</section>

<section>
  <h2 class="abs h" style="left:322px;top:636px;font-size:20px">Our <span>Gallery</span></h2>
  <div class="abs arrows" style="left:806px;top:643px">
    <svg width="9" height="13" viewBox="0 0 9 13"><path d="M7 1L2 6.5 7 12" fill="none" stroke="#444" stroke-width="1.5"/></svg>
    <svg width="9" height="13" viewBox="0 0 9 13"><path d="M2 1l5 5.5L2 12" fill="none" stroke="#444" stroke-width="1.5"/></svg>
  </div>
  <div class="abs photo" style="left:322px;top:673px;width:163px;height:99px;background:linear-gradient(180deg,#8a8f86,#6d8f52 45%,#4d7a2e)" role="img" aria-label="Photo of greenhouse interior with raised growing beds"></div>
  <div class="abs photo" style="left:498px;top:673px;width:163px;height:99px;background:linear-gradient(160deg,#7faa5a,#4a7f32)" role="img" aria-label="Photo of a large leafy cannabis plant"></div>
  <div class="abs photo" style="left:674px;top:673px;width:162px;height:99px;background:linear-gradient(160deg,#a9c48a,#4e8a36 55%,#1f2a1e)" role="img" aria-label="Photo of seedlings in pots with plant labels"></div>
  <div class="abs divider"></div>

  <h2 class="abs h" style="left:322px;top:807px;font-size:20px">Latest <span>News</span></h2>
  <div class="abs arrows" style="left:806px;top:814px">
    <svg width="9" height="13" viewBox="0 0 9 13"><path d="M7 1L2 6.5 7 12" fill="none" stroke="#444" stroke-width="1.5"/></svg>
    <svg width="9" height="13" viewBox="0 0 9 13"><path d="M2 1l5 5.5L2 12" fill="none" stroke="#444" stroke-width="1.5"/></svg>
  </div>

  <div class="abs photo thumb" style="left:322px;top:853px;background:linear-gradient(160deg,#e9e2d6,#b9a88f 60%,#6f9a3e)" role="img" aria-label="Photo of a seedling held in cupped hands"></div>
  <div class="abs news" style="left:410px;top:851px;width:160px">
    <div class="date">Dec25, 2014</div>
    <p>Aliquam molestie, mi et imperdiet euismod, dui purus auctor tellus, et interdum lacus lectus et ante..</p>
    <div class="more">Read More</div>
  </div>

  <div class="abs photo thumb" style="left:590px;top:853px;background:linear-gradient(160deg,#8fb86a,#4f8a34 60%,#2f4f22)" role="img" aria-label="Photo of a grower standing among tall plants"></div>
  <div class="abs news" style="left:677px;top:851px;width:160px">
    <div class="date">Dec25, 2014</div>
    <p>Aliquam molestie, mi et imperdiet euismod, dui purus auctor tellus, et interdum lacus lectus et ante..</p>
    <div class="more">Read More</div>
  </div>
</section>

<section>
  <h2 class="abs h" style="left:55px;top:980px;font-size:20px">Our <span>Testimonials</span></h2>
  <svg class="abs" style="left:57px;top:1016px" width="22" height="13" viewBox="0 0 22 13"><path d="M0 13V7C0 3 2 .5 6 0v3C4 3.5 3.5 5 3.5 6H9v7zM12 13V7c0-4 2-6.5 6-7v3c-2 .5-2.5 2-2.5 3H21v7z" fill="#bdbdbd"/></svg>
  <p class="abs quote" style="left:55px;top:1015px;width:480px;text-indent:32px">Aliquam molestie, mi et imperdiet euismod, dui purus auctor tellus, et interdum lacus lectus et ante. Sed accumsan sollicitudin sapien, sit amet adipiscing turpis gravida ac. In congue, neque ac lobortis volutpat, libero mauris varius mi, vitae suscipit ipsum ligula vitae risus. Duis aliquam nibh a dui iaculis viverra id a velit..</p>
  <div class="abs" style="left:55px;top:1069px;font-size:9.6px;font-style:italic;color:var(--orange)">-Name goes here</div>
  <div class="abs" style="left:55px;top:1082px;font-size:9.6px;font-style:italic;color:var(--green)">Location</div>

  <div class="abs rent">
    <h3>View our rent space<br>locations</h3>
    <a class="get">Get Location</a>
    <div class="mapart" role="img" aria-label="Illustration of a folded map with a location pin"></div>
  </div>
</section>

<footer class="abs footer">
  <div class="fbrand"><i></i>Verdale Lodge 37</div>
  <small>Copyright © 2014. All Right Reserved &nbsp;| &nbsp;Term of Services</small>
  <div class="connect">CONNECT US:
    <i style="background:#3b5a98"></i><i style="background:#4aa9d8"></i><i style="background:#c9342a"></i>
  </div>
</footer>

</body>
</html>
```